KLV Plant Services

We are a heavy diesel mechanical business with additional air con certificates, remapping engine rebuilt

Contact Information for Business Card

Company Name, Director Name, Managing Director, Contact details, email and website

Font styles to use
Serif
Script

```html
<!DOCTYPE html>
<html lang="en">
<head>
<meta charset="utf-8">
<title>KLV Plant Services – Business Card</title>
<link rel="stylesheet" href="https://fonts.googleapis.com/css2?family=Arimo:wght@400;700&display=swap">
<style>
  :root {
    --navy: #0b0a5e;
    --navy-deep: #06054f;
    --ink: #2b2b2b;
    --muted: #6c6c6c;
    --paper: #f6f6f6;
    --backdrop: #9a9a9a;
  }
  * { box-sizing: border-box; margin: 0; padding: 0; }
  html, body { width: 1200px; height: 1050px; overflow: hidden; }
  body {
    background: var(--backdrop);
    font-family: "Arimo", Arial, sans-serif;
    position: relative;
  }
  .card {
    position: absolute;
    left: 190px;
    width: 820px;
    height: 468px;
    border-radius: 34px;
    box-shadow: 0 10px 24px rgba(0,0,0,0.25);
  }
  .card--front {
    top: 37px;
    background: var(--paper);
    border: 4px solid var(--navy);
  }
  .card--back {
    top: 545px;
    background: var(--navy-deep);
    border: 4px solid #ffffff;
    display: flex;
    align-items: center;
    justify-content: center;
  }

  .brand-mark {
    position: absolute;
    top: 120px;
    right: 60px;
    display: flex;
    align-items: center;
    gap: 12px;
    color: var(--navy);
    font-weight: 700;
    font-size: 28px;
  }
  .brand-mark__dot {
    width: 22px; height: 22px;
    border-radius: 50%;
    background: var(--navy);
  }

  .contact {
    position: absolute;
    left: 70px;
    top: 200px;
    color: var(--ink);
    font-size: 17px;
    line-height: 1.35;
  }
  .contact__name {
    color: var(--navy);
    font-weight: 700;
    font-size: 30px;
    line-height: 1.1;
  }
  .contact__role {
    color: var(--muted);
    font-size: 18px;
    margin-bottom: 8px;
  }
  .contact__label {
    color: var(--navy);
    font-weight: 700;
    margin-right: 4px;
  }
  .contact__row {
    display: flex;
    align-items: flex-start;
    margin-top: 14px;
    gap: 22px;
  }
  .contact__divider {
    width: 1.5px;
    align-self: stretch;
    background: var(--ink);
    margin-top: 20px;
  }
  .contact__online { padding-top: 34px; }

  .brand-wordmark {
    color: #ffffff;
    font-weight: 700;
    font-size: 60px;
    letter-spacing: 0.5px;
  }
</style>
</head>
<body>
  <section class="card card--front" aria-label="Card front">
    <div class="brand-mark">
      <span class="brand-mark__dot"></span>
      <span>KLV Plant Services</span>
    </div>

    <div class="contact">
      <div class="contact__name">Owen Hartley</div>
      <div class="contact__role">Managing Director</div>
      <div><span class="contact__label">P :</span>(555) 0142-7719</div>
      <div class="contact__row">
        <div class="contact__address">
          27 Harrow Lane<br>
          Millbrook, NY 12545
        </div>
        <div class="contact__divider"></div>
        <div class="contact__online">
          <div><span class="contact__label">E :</span>name@klvplant.com</div>
          <div><span class="contact__label">W :</span>www.klvplant.com</div>
        </div>
      </div>
    </div>
  </section>

  <section class="card card--back" aria-label="Card back">
    <div class="brand-wordmark">KLV Plant Services</div>
  </section>
</body>
</html>
```